Design my dad a new business card because his current one sucks!

I need a business card designed for my fathers home maintenance business. His customers are individuals (single moms, old people etc.) as well as the occasional business. As such it needs to be accessible to both target audiences.

The front of the card should be dark grey on yellow with the logo and contain the following information:
- Darren Holtwick
- 0488 274 915
- info@brightoakhomecare.com.au
- 0488 274 915

- ABN: 71 284 630 912
- 'Fully Insured'

The reverse should be yellow on dark grey and will have the web address:
- brightoakhomecare.com.au

And a few key services he offers:
GENERAL REPAIRS
PAINTING/TILING/
PAVING &CONCRETING
PRESSURE WASHING
ON-SITE WELDING
DECKING ADDITIONS & REPAIRS
FENCING
FULL BOND CLEANING

This will be first time the logo has been printed so you will need to come up with the best CMYK approximation of the RGB colours to make sure it is a close as possible.

```html
<!DOCTYPE html>
<html lang="en">
<head>
<meta charset="utf-8">
<title>Bright Oak Home Care – Business Card</title>
<link rel="stylesheet" href="https://fonts.googleapis.com/css2?family=Open+Sans:wght@400;700&display=swap">
<style>
  :root {
    --yellow-core: #fff200;
    --yellow-edge: #f7c300;
    --ink-dark: #231f20;
    --ink-grey: #58595b;
    --band-grey: #353130;
    --white: #ffffff;
  }
  html, body {
    margin: 0;
    padding: 0;
    width: 1200px;
    height: 686px;
    overflow: hidden;
    background: #ffffff;
  }
  .card {
    position: relative;
    width: 1200px;
    height: 686px;
    overflow: hidden;
    font-family: "Open Sans", Arial, sans-serif;
    background: radial-gradient(ellipse 760px 560px at 590px 290px, var(--yellow-core) 0%, #fde300 45%, var(--yellow-edge) 100%);
  }
  .tilted {
    position: absolute;
    margin: 0;
    line-height: 1;
    white-space: nowrap;
    transform-origin: 0 100%;
    transform: rotate(-30deg);
  }
  .brand-name {
    left: 32px;
    top: 392px;
    font-size: 58px;
    font-weight: 700;
    color: var(--ink-dark);
    letter-spacing: 0.5px;
  }
  .brand-note {
    left: 456px;
    top: 278px;
    font-size: 25px;
    font-weight: 400;
    color: var(--ink-grey);
  }
  .holder-name {
    left: 42px;
    top: 598px;
    font-size: 50px;
    font-weight: 700;
    color: var(--ink-grey);
  }
  .contact-phone,
  .contact-email,
  .contact-web {
    font-size: 32px;
    font-weight: 400;
    color: var(--ink-grey);
  }
  .contact-phone { left: 482px; top: 500px; }
  .contact-email { left: 516px; top: 563px; }
  .contact-web   { left: 790px; top: 306px; }
  .icon {
    position: absolute;
    transform-origin: 50% 50%;
    transform: rotate(-30deg);
  }
  .icon-phone { left: 368px; top: 535px; width: 66px; height: 56px; }
  .icon-mail  { left: 404px; top: 600px; width: 64px; height: 44px; }
  .dark-band {
    position: absolute;
    left: 0;
    top: 0;
    width: 1200px;
    height: 686px;
  }
  .band-email {
    left: 628px;
    top: 646px;
    font-size: 31px;
    font-weight: 400;
    color: var(--white);
  }
  .abn {
    position: absolute;
    right: 22px;
    bottom: 12px;
    margin: 0;
    font-size: 24px;
    font-weight: 400;
    color: var(--white);
    line-height: 1;
  }
</style>
</head>
<body>
  <div class="card">
    <svg class="dark-band" viewBox="0 0 1200 686" aria-hidden="true">
      <polygon points="540,686 1200,300 1200,686" fill="var(--band-grey)"/>
    </svg>

    <p class="tilted brand-name">Bright Oak Home Care</p>
    <p class="tilted brand-note">Fully Insured</p>

    <p class="tilted holder-name">Darren Holtwick</p>

    <svg class="icon icon-phone" viewBox="0 0 66 56" aria-hidden="true">
      <g fill="none" stroke="var(--ink-grey)" stroke-width="2.4" stroke-linejoin="round" stroke-linecap="round">
        <path d="M6 16 C6 6 60 6 60 16 L60 21 L48 21 L46 15 C38 12 28 12 20 15 L18 21 L6 21 Z"/>
        <path d="M18 24 L48 24 L56 50 L10 50 Z"/>
        <circle cx="33" cy="37" r="7.5"/>
        <circle cx="33" cy="37" r="2"/>
      </g>
    </svg>
    <p class="tilted contact-phone">0488 274 915</p>

    <svg class="icon icon-mail" viewBox="0 0 64 44" aria-hidden="true">
      <g fill="none" stroke="var(--ink-grey)" stroke-width="2.4" stroke-linejoin="round">
        <rect x="3" y="3" width="58" height="38" rx="2"/>
        <path d="M3 3 L32 26 L61 3"/>
        <path d="M3 41 L24 20 M61 41 L40 20"/>
      </g>
    </svg>
    <p class="tilted contact-email">info@brightoakhomecare.com.au</p>

    <p class="tilted contact-web">brightoakhomecare.com.au</p>

    <p class="tilted band-email">info@brightoakhomecare.com.au</p>
    <p class="abn">ABN: 71 284 630 912</p>
  </div>
</body>
</html>
```